Etikett für Rotweinflasche
Liebe farbkosmos Atelier, wir werden uns bei der endgültigen Etikettengestaltung (finale Größe + Rückseite) noch an Euch melden. Bitte sendet uns euren Kontakt an helga.brandt@morvelli.wine
Zielgruppe
Morvelli Italia ist ein exklusives Boutique-Weingut in Sizilien, das hochqualitative Spitzenweine in kleinen Mengen mit modernster Technologie und stets nachhaltig erzeugt. Wir hinterfragen sowohl in der Agronomie im Weingarten als auch in der Önologie im Weinkeller alle herrschenden Traditionen und trachten danach, stets das beste Endprodukt zu kreieren. Der vulkanische, kalkreiche Boden Siziliens sowie trockene, sonnenreiche und niederschlagsarme Vegetationsperioden sind unsere optimale Basis.
Zielgruppe: Internationale Genussmenschen jeglichen Alters, die sich bewusst auch höherpreisige Weine (um die €30+) gönnen , vor allem kunstaffine young professionals mit Qualitäts-& Nachhaltigkeitsanspruch
Aufgabenstellung
Das Etikett ist für Rotwein-Flaschen (Cabernet Sauvignon / Nero D'Avola / Frappato / Syrah / Cerasuolo / Petit Verdot / sowie einen Bourdeaux-Cuveè aus Cabernet Sauvignon und Petit Verdot) .
Die Flasche ist reinschwarz, sehr hochwertig und schwer.
Flaschenform: Bordeauxflasche siehe technisches Datenblatt
Sleeve über dem Korken: schwarz mit weißer Schrift wie bisher
Zu gestalten ist das Etikett der Vorderseite. Zumindest die jeweilige Rotwein-Sorte ist auch textlich darzustellen (zwecks Scannen mit Trubel-App)
Der Kreativität kann freien Lauf gelassen werden! Unterscheidbarkeit vom Markt ist explizit gewollt.
Unsere aktuellen Etiketten und Markenauftritt siehe: https://morvelli.wine/shop/

```html
<!DOCTYPE html>
<html lang="de">
<head>
<meta charset="utf-8">
<title>Syrah – Etikett</title>
<link rel="stylesheet" href="https://fonts.googleapis.com/css2?family=Courier+Prime:wght@700&display=swap">
<style>
  :root {
    --canvas-bg: #141414;
    --label-magenta: #d8336a;
    --label-red: #e4493a;
    --label-orange: #ea7a3c;
    --label-yellow: #e7c84a;
    --label-purple: #5a1f4a;
    --label-haze: #9a6a8a;
    --ink-white: #ffffff;
    --ghost-white: rgba(255, 235, 235, 0.45);
  }
  * { margin: 0; padding: 0; box-sizing: border-box; }
  html, body {
    width: 1200px;
    height: 1200px;
    overflow: hidden;
    background: var(--canvas-bg);
  }
  .canvas {
    position: relative;
    width: 1200px;
    height: 1200px;
    display: flex;
    align-items: center;
    justify-content: center;
  }
  .wine-label {
    position: relative;
    width: 712px;
    height: 1000px;
    overflow: hidden;
    background: var(--label-red);
  }
  .label-artwork {
    position: absolute;
    inset: 0;
    background:
      radial-gradient(ellipse 30% 22% at 96% 4%, var(--label-purple) 0%, rgba(90,31,74,0) 100%),
      radial-gradient(ellipse 55% 30% at 45% 12%, var(--label-magenta) 0%, rgba(216,51,106,0) 100%),
      radial-gradient(ellipse 45% 30% at 10% 18%, #e85a3a 0%, rgba(232,90,58,0) 100%),
      radial-gradient(ellipse 60% 30% at 75% 48%, var(--label-orange) 0%, rgba(234,122,60,0) 100%),
      radial-gradient(ellipse 45% 28% at 20% 68%, var(--label-haze) 0%, rgba(154,106,138,0) 100%),
      radial-gradient(ellipse 70% 40% at 65% 78%, var(--label-yellow) 0%, rgba(231,200,74,0) 100%),
      linear-gradient(180deg, #de3e4e 0%, #e25a3c 40%, #df9a48 75%, #c9b14e 100%);
  }
  .variety-name {
    position: absolute;
    top: 136px;
    left: 0;
    right: 0;
    text-align: center;
    font-family: "Courier Prime", "Courier New", monospace;
    font-weight: 700;
    font-size: 64px;
    line-height: 1;
    color: var(--ink-white);
    letter-spacing: 1px;
  }
  .estate-name {
    position: absolute;
    top: 360px;
    left: 48px;
    font-family: "Courier Prime", "Courier New", monospace;
    font-weight: 700;
    font-size: 64px;
    line-height: 1;
    color: var(--ghost-white);
    white-space: nowrap;
  }
</style>
</head>
<body>
  <main class="canvas">
    <section class="wine-label">
      <div class="label-artwork" role="img" aria-label="Abstrakte Farbwolke wie ein Nebel im Weltall, von Magenta oben über Orange bis Gelb unten"></div>
      <h1 class="variety-name">Syrah</h1>
      <p class="estate-name">Morvelli</p>
    </section>
  </main>
</body>
</html>
```